Business Card Design

New business card design

Target Market(s)

Residential & Commercial Property Managers

Industry/Entity Type

Plumbing Services

Contact Information for Business Card

Name - Rowan Keddle, title - Director, Phone Number - 0431 286 517, email - rowan@tbk-plumbing.com.au, Company ABN - 73 215 904 386,

Font styles to use
Sans Serif

Colors
0054AA
0677BA
7BADD7
CADEEF
E8F1F8

```html
<!DOCTYPE html>
<html lang="en">
<head>
<meta charset="utf-8">
<title>TBK Plumbing Services – Business Card</title>
<link rel="stylesheet" href="https://fonts.googleapis.com/css2?family=Montserrat:wght@400;500;700&display=swap">
<style>
  :root {
    --stage: #222222;
    --card-white: #ffffff;
    --brand-blue: #29a9e1;
    --brand-blue-light: #6ccaf4;
    --brand-blue-deep: #0677ba;
    --ink: #1c2329;
    --muted: #6b5b52;
  }
  * { box-sizing: border-box; margin: 0; padding: 0; }
  html, body { width: 1200px; height: 780px; overflow: hidden; }
  body {
    background: var(--stage);
    font-family: "Montserrat", Arial, sans-serif;
    display: flex;
    align-items: center;
    justify-content: center;
    gap: 40px;
  }
  .card {
    position: relative;
    width: 540px;
    height: 310px;
    border-radius: 26px;
    overflow: hidden;
    border-bottom: 4px solid var(--brand-blue);
  }
  /* Back side */
  .card--back {
    background: var(--brand-blue);
  }
  .card--back .pattern-area {
    position: absolute;
    inset: 0;
    background: linear-gradient(110deg, var(--brand-blue-light) 0%, var(--brand-blue) 50%, var(--brand-blue-deep) 100%);
  }
  /* Front side */
  .card--front {
    background: var(--card-white);
  }
  .brand {
    position: absolute;
    left: 34px;
    top: 34px;
  }
  .brand__row {
    display: flex;
    align-items: center;
    gap: 10px;
  }
  .brand__name {
    font-size: 72px;
    font-weight: 500;
    color: var(--ink);
    line-height: 1;
    letter-spacing: 2px;
  }
  .brand__dot {
    width: 16px;
    height: 16px;
    border-radius: 50%;
    background: var(--brand-blue);
    margin-top: 30px;
  }
  .brand__tagline {
    margin-top: 8px;
    font-size: 11px;
    letter-spacing: 9px;
    color: var(--muted);
    font-weight: 400;
  }
  .person {
    position: absolute;
    left: 34px;
    top: 170px;
    padding-left: 14px;
    border-left: 8px solid var(--brand-blue);
  }
  .person__name {
    font-size: 22px;
    font-weight: 700;
    color: var(--brand-blue);
    line-height: 1.15;
  }
  .person__title {
    font-size: 15px;
    color: var(--ink);
  }
  .contact {
    position: absolute;
    left: 56px;
    top: 238px;
    list-style: none;
    font-size: 14px;
    color: var(--ink);
  }
  .contact__item {
    display: flex;
    align-items: center;
    gap: 8px;
    margin-bottom: 5px;
  }
  .contact__icon { width: 14px; height: 14px; flex: none; }
  .abn {
    position: absolute;
    right: 30px;
    bottom: 50px;
    font-size: 14px;
    color: var(--ink);
  }
</style>
</head>
<body>
  <section class="card card--back" aria-label="Card back">
    <div class="pattern-area" role="img" aria-label="Repeating water-drop pattern in light to deep blue"></div>
  </section>

  <section class="card card--front" aria-label="Card front">
    <div class="brand">
      <div class="brand__row">
        <span class="brand__name">tbk</span>
        <span class="brand__dot"></span>
      </div>
      <p class="brand__tagline">plumbing services</p>
    </div>

    <div class="person">
      <p class="person__name">Rowan Keddle</p>
      <p class="person__title">Director</p>
    </div>

    <ul class="contact">
      <li class="contact__item">
        <svg class="contact__icon" viewBox="0 0 24 24" aria-hidden="true"><path fill="#29a9e1" d="M6.6 10.8a15.1 15.1 0 0 0 6.6 6.6l2.2-2.2a1 1 0 0 1 1-.25 11.4 11.4 0 0 0 3.6.57 1 1 0 0 1 1 1V20a1 1 0 0 1-1 1A17 17 0 0 1 3 4a1 1 0 0 1 1-1h3.5a1 1 0 0 1 1 1c0 1.25.2 2.45.57 3.6a1 1 0 0 1-.25 1z"/></svg>
        <span>0431 286 517</span>
      </li>
      <li class="contact__item">
        <svg class="contact__icon" viewBox="0 0 24 24" aria-hidden="true"><rect x="2" y="5" width="20" height="14" rx="2" fill="#29a9e1"/><path d="M3 6l9 7 9-7" fill="none" stroke="#fff" stroke-width="1.6"/></svg>
        <span>rowan@tbk-plumbing.com.au</span>
      </li>
    </ul>

    <p class="abn">Company ABN - 73 215 904 386</p>
  </section>
</body>
</html>
```